Bry7Legal Letterhead

Need a new letterhead for my law firm.
IDENTIFYING INFORMATION BELOW:
Anselmo R Quintara III
Attorney at Law
Address: 2847 Larkspur Blvd, Ste 300, Dallas, TX 75204
Phone: 877-482-6017
Fax: 469-738-1452
Email: bry@bry7legal.example
Website: www.bry7legal.example

Colors
0054AA
0677BA
7BADD7
CADEEF
E8F1F8

Requirements
Must have
• Logo needs to be on the letterhead, along with identifying information which is included in the project description.

```html
<!DOCTYPE html>
<html lang="en">
<head>
<meta charset="utf-8">
<title>Bry7Legal Letterhead</title>
<link href="https://fonts.googleapis.com/css2?family=Arimo:wght@400;700&display=swap" rel="stylesheet">
<style>
:root{
  --bg:#bdbdbd;
  --paper:#ffffff;
  --band-top:#e9eaec;
  --band-bottom:#f6f6f7;
  --ink:#1b1b1b;
  --muted:#4a4a4a;
  --blue-deep:#0054aa;
  --blue:#0677ba;
  --blue-light:#1aa3e0;
  --stripe:#1f1f1f;
}
*{margin:0;padding:0;box-sizing:border-box}
html,body{width:1200px;height:1089px;overflow:hidden}
body{background:var(--bg);font-family:"Arimo",Arial,sans-serif;color:var(--ink);position:relative}
.letterhead{position:absolute;left:214px;top:40px;width:772px;height:1000px;background:var(--paper);overflow:hidden;box-shadow:0 6px 24px rgba(0,0,0,.25)}
.header-band{position:absolute;left:0;top:0;width:772px;height:200px}
.logo{position:absolute;right:44px;top:58px;font-weight:700;font-size:40px;letter-spacing:1px;color:var(--ink)}
.date{position:absolute;left:70px;top:168px;font-size:14px}
.recipient{position:absolute;left:70px;top:204px;font-size:14px;line-height:20px}
.recipient strong{font-weight:700}
.letter-body{position:absolute;left:70px;top:310px;width:640px;font-size:14.5px;line-height:21px}
.letter-body p{margin-bottom:12px;text-align:justify}
.signature{position:absolute;left:70px;top:560px}
.signature-mark{display:block;width:110px;height:34px;margin-top:6px}
.signer{font-weight:700;font-size:17px;margin-top:4px}
.footer-contact{position:absolute;left:70px;top:800px;display:flex;gap:36px;font-size:13px;line-height:19px;color:var(--muted)}
.footer-name{color:var(--blue);font-weight:700;font-size:15px}
.contact-list{list-style:none;padding-top:19px}
.contact-list li{display:flex;align-items:center;gap:6px}
.contact-list svg{width:12px;height:12px;fill:var(--blue)}
.corner{position:absolute;right:0;bottom:0;width:772px;height:1000px;pointer-events:none}
</style>
</head>
<body>
<main class="letterhead">
  <svg class="header-band" viewBox="0 0 772 200" aria-hidden="true">
    <defs>
      <linearGradient id="bandFill" x1="0" y1="0" x2="0" y2="1">
        <stop offset="0" stop-color="var(--band-top)"/>
        <stop offset="1" stop-color="var(--band-bottom)"/>
      </linearGradient>
    </defs>
    <path d="M0 0H772V150C560 200 300 160 0 30Z" fill="url(#bandFill)"/>
  </svg>

  <div class="logo">Bry7Legal</div>

  <div class="date">4th September 20XX</div>
  <address class="recipient" style="font-style:normal">
    <strong>Ronny Reader</strong><br>
    CEO, Company Name<br>
    123 Address St.<br>
    Anytown, ST 12345
  </address>

  <section class="letter-body">
    <p>Dear Mr. Reader,<br>Lorem ipsum dolor sit amet, consectetuer adipiscing elit, sed diam nonummy nibh euismod tincidunt ut laoreet dolore magna aliquam erat volutpat. Ut wisi enim ad minim veniam, quis nostrud exerci tation ullamcorper suscipit lobortis nisl ut aliquip ex ea commodo consequat.</p>
    <p>Duis autem vel eum iriure dolor in hendrerit in vulputate velit esse molestie consequat, vel illum dolore eu feugiat nulla facilisis at vero eros et accumsan.</p>
    <p>Nam liber tempor cum soluta nobis eleifend option congue nihil imperdiet doming id quod mazim placerat facer possim assum. Typi non habent claritatem insitam; est usus legentis in iis qui facit eorum claritatem. Investigationes demonstraverunt lectores legere me lius quod ii legunt saepius.</p>
  </section>

  <div class="signature">
    <div>Sincerely,</div>
    <svg class="signature-mark" viewBox="0 0 110 34" role="img" aria-label="Handwritten signature">
      <rect width="110" height="34" rx="3" fill="#f0f0f0"/>
    </svg>
    <div class="signer">Your Name</div>
  </div>

  <footer class="footer-contact">
    <div>
      <div class="footer-name">Anselmo R Quintara III</div>
      <div>Attorney at Law</div>
      <div>2847 Larkspur Blvd, Ste 300</div>
      <div>Dallas, TX 75204</div>
    </div>
    <ul class="contact-list">
      <li><svg viewBox="0 0 12 12"><path d="M3 1l2 2.5-1 1.2c.6 1.3 1.6 2.3 2.9 2.9l1.2-1L11 8.6 9.8 10.8C5.3 10.6 1.4 6.7 1.2 2.2Z"/></svg>877-482-6017</li>
      <li><svg viewBox="0 0 12 12"><path d="M3 1h5v3H3zM1 5h10v5H9V8H3v2H1zM3 9h6v2H3z"/></svg>469-738-1452</li>
      <li><svg viewBox="0 0 12 12"><path d="M1 3h10v6H1zM1.5 3.5 6 7l4.5-3.5" stroke="#fff" stroke-width=".8"/></svg>bry@bry7legal.example</li>
      <li><svg viewBox="0 0 12 12"><circle cx="6" cy="6" r="5"/><path d="M1 6h10M6 1c2 2.5 2 7.5 0 10M6 1c-2 2.5-2 7.5 0 10" stroke="#fff" stroke-width=".7" fill="none"/></svg>www.bry7legal.example</li>
    </ul>
  </footer>

  <svg class="corner" viewBox="0 0 772 1000" aria-hidden="true">
    <defs>
      <radialGradient id="cornerFill" cx="0.45" cy="0.25" r="0.8">
        <stop offset="0" stop-color="var(--blue-light)"/>
        <stop offset="0.6" stop-color="var(--blue)"/>
        <stop offset="1" stop-color="var(--blue-deep)"/>
      </radialGradient>
    </defs>
    <path d="M432 1000L772 868V874L445 1000Z" fill="var(--stripe)"/>
    <path d="M455 1000L772 880V1000Z" fill="url(#cornerFill)"/>
  </svg>
</main>
</body>
</html>
```